Business card design for Automotive workshop

We need a business card for a new automotive repair and tyre shop called Keelstone Prime Automotive located in New Zealand. We are a clean, modern and fresh workshop and company.

Front needs to feature logo,
my name:
Marlo Fenwicke (director)

Address:
48 Tarn Lane
Harrowvale 3592

Phone: 07 594 2713
Mobile: 027 451 9362
Email: office@keelstoneautomotive.example.nz
Website: keelstoneautomotive.example.nz

Back needs to feature an area to write down appointment details, date and time.

Also feature a list of jobs and work we do such as,
Vehicle Servicing
All Mechanical Repairs
Warrant of Fitness
Tyres & Wheel Alignments
Automotive Diagnostics
Automotive Parts & Supplies

```html
<!DOCTYPE html>
<html lang="en">
<head>
<meta charset="utf-8">
<title>Keelstone Prime Automotive — Business Card</title>
<link rel="stylesheet" href="https://fonts.googleapis.com/css2?family=Open+Sans:ital,wght@0,400;0,600;0,700;1,400;1,600;1,700&display=swap">
<style>
  :root {
    --red: #e31c25;
    --black: #121212;
    --panel: #333333;
    --white: #ffffff;
    --ink: #1e1e1e;
    --backdrop: #4a4542;
    --muted: #bdbdbd;
  }
  * { box-sizing: border-box; margin: 0; padding: 0; }
  html, body { width: 1200px; height: 810px; overflow: hidden; }
  body {
    background: var(--backdrop);
    font-family: "Open Sans", Arial, sans-serif;
    position: relative;
  }
  .card {
    position: absolute;
    width: 560px;
    height: 320px;
    box-shadow: 0 10px 28px rgba(0,0,0,.45);
    overflow: hidden;
  }

  /* Back side */
  .card-back { left: 40px; top: 60px; background: var(--black); color: var(--white); }
  .appointment-panel {
    position: absolute; left: 40px; right: 40px; top: 34px; height: 96px;
    background: var(--panel);
  }
  .appointment-title {
    position: absolute; left: 0; right: 0; top: 46px;
    text-align: center; color: var(--red);
    font-weight: 700; font-style: italic; font-size: 20px; line-height: 28px;
  }
  .appointment-fields {
    position: absolute; left: 40px; right: 40px; top: 150px;
    display: flex; gap: 24px; font-weight: 700; font-style: italic; font-size: 14px;
  }
  .field { flex: 1; display: flex; align-items: flex-end; gap: 8px; }
  .field-line { flex: 1; border-bottom: 1px dashed var(--muted); margin-bottom: 4px; }
  .works-heading {
    position: absolute; left: 0; right: 0; top: 196px;
    display: flex; align-items: center; justify-content: center; gap: 12px;
    font-weight: 700; font-style: italic; font-size: 13px;
  }
  .works-heading .rule { width: 70px; height: 1.5px; background: var(--red); }
  .works-list {
    position: absolute; left: 20px; right: 20px; top: 232px;
    list-style: none; display: flex; flex-wrap: wrap; justify-content: center;
    gap: 10px 16px; font-style: italic; font-size: 12.5px;
  }
  .works-list li::before { content: "●"; color: var(--red); font-size: 8px; margin-right: 4px; vertical-align: 2px; }

  /* Front side */
  .card-front { left: 600px; top: 430px; background: var(--white); color: var(--ink); }
  .brand {
    position: absolute; right: 36px; top: 42px;
    display: flex; align-items: center; gap: 10px;
    color: var(--red); font-weight: 700; font-size: 22px; letter-spacing: .5px;
  }
  .brand-mark { width: 14px; height: 14px; background: var(--red); }
  .person {
    position: absolute; left: 30px; top: 140px; width: 220px; text-align: right;
  }
  .person-name { color: var(--red); font-weight: 700; font-size: 21px; }
  .person-role { font-size: 13px; margin-top: 2px; }
  .divider { position: absolute; left: 268px; top: 136px; width: 1px; height: 76px; background: var(--red); }
  .contacts {
    position: absolute; left: 282px; top: 132px; list-style: none;
    font-size: 12.5px; line-height: 20px;
  }
  .contacts li { display: flex; align-items: center; gap: 8px; }
  .contacts svg { width: 11px; height: 11px; fill: var(--red); flex: none; }
  .address-band {
    position: absolute; left: 0; right: 0; bottom: 22px; height: 36px;
    background: var(--red); color: var(--white);
    display: flex; align-items: center; padding-left: 180px; font-size: 14px;
  }
</style>
</head>
<body>

<section class="card card-back" aria-label="Card back">
  <div class="appointment-panel"></div>
  <h2 class="appointment-title">Appointment Details</h2>
  <div class="appointment-fields">
    <div class="field"><span>Date</span><span class="field-line"></span></div>
    <div class="field"><span>Time</span><span class="field-line"></span></div>
  </div>
  <h3 class="works-heading"><span class="rule"></span>Our Works<span class="rule"></span></h3>
  <ul class="works-list">
    <li>Vehicle Servicing</li>
    <li>Warrant of Fitness</li>
    <li>Automotive Parts &amp; Supplies</li>
    <li>Automotive Diagnostics</li>
    <li>Tyres &amp; Wheel Alignments</li>
    <li>All Mechanical Repairs</li>
  </ul>
</section>

<section class="card card-front" aria-label="Card front">
  <div class="brand"><span class="brand-mark"></span>KEELSTONE PRIME AUTOMOTIVE</div>
  <div class="person">
    <div class="person-name">Marlo Fenwicke</div>
    <div class="person-role">Director</div>
  </div>
  <div class="divider"></div>
  <ul class="contacts">
    <li><svg viewBox="0 0 12 12"><path d="M2 1h2.5l1 3-1.5 1a7 7 0 0 0 3 3l1-1.5 3 1V10a1 1 0 0 1-1 1A9 9 0 0 1 1 2a1 1 0 0 1 1-1z"/></svg>07 594 2713</li>
    <li><svg viewBox="0 0 12 12"><path d="M3.5 0h5A1 1 0 0 1 9.5 1v10a1 1 0 0 1-1 1h-5a1 1 0 0 1-1-1V1a1 1 0 0 1 1-1zM4 1.5v7.5h4V1.5z"/></svg>027 451 9362</li>
    <li><svg viewBox="0 0 12 12"><path d="M0 2h12v8H0zM1 3v.4l5 3.2 5-3.2V3z"/></svg>office@keelstoneautomotive.example.nz</li>
    <li><svg viewBox="0 0 12 12"><path d="M6 0a6 6 0 1 0 0 12A6 6 0 0 0 6 0zm0 1.2a4.8 4.8 0 0 1 0 9.6 4.8 4.8 0 0 1 0-9.6zM3 5h6v2H3z"/></svg>keelstoneautomotive.example.nz</li>
  </ul>
  <div class="address-band">48 Tarn Lane Harrowvale 3592</div>
</section>

</body>
</html>
```